At Home Pet Euthanasia - business cards & brand stationary

We already have a logo and the colors and a website. Need a business card designed that will be able to customized to multiple veterinarians who will be partnering with us. The feel needs to be compassionate, comforting with our tagline 'A Gift of Love at Home'. It will be 2 sides.
On the back our platform/partner vets will be customizing each business card with their own service areas, phone numbers, name and title. On the front, i would like to see experimentation with use of our photos, the logo, tagline and a description 'Peaceful and Compassionate At-Home Pet Euthanasia'

```html
<!DOCTYPE html>
<html lang="en">
<head>
<meta charset="UTF-8">
<title>Hearthwell Business Card</title>
<link rel="stylesheet" href="https://fonts.googleapis.com/css2?family=Raleway:wght@300;400;600;700&family=Parisienne&display=swap">
<style>
  :root {
    --backdrop: #2b2b2b;
    --brand-blue: #7397c2;
    --paper-white: #ffffff;
    --photo-dark: #1c1c1c;
    --photo-mid: #5a5a5a;
    --photo-light: #9a9a9a;
  }
  * { box-sizing: border-box; margin: 0; padding: 0; }
  html, body {
    width: 1200px; height: 960px; overflow: hidden;
    background: var(--backdrop);
    font-family: "Raleway", sans-serif;
  }
  .stage {
    width: 1200px; height: 960px;
    display: flex; flex-direction: column; align-items: center; justify-content: center; gap: 40px;
  }
  .card {
    position: relative; width: 720px; height: 410px;
    border-radius: 24px; overflow: hidden;
    box-shadow: 0 14px 30px rgba(0,0,0,.45);
  }
  /* Front */
  .card-front { background: var(--photo-dark); }
  .photo-area {
    position: absolute; inset: 0;
    background: radial-gradient(ellipse at 32% 48%, var(--photo-light) 0%, var(--photo-mid) 35%, var(--photo-dark) 80%);
  }
  .front-brand {
    position: absolute; left: 420px; top: 60px; width: 260px;
    color: var(--paper-white); text-align: center;
  }
  .wordmark {
    display: inline-flex; align-items: center; gap: 10px;
    font-weight: 700; font-size: 44px; letter-spacing: .5px;
  }
  .wordmark-dot {
    width: 16px; height: 16px; border-radius: 50%; background: currentColor; display: inline-block;
  }
  .tagline { font-weight: 400; font-size: 13px; margin-top: 2px; }
  .description {
    position: absolute; left: 400px; top: 200px; width: 300px;
    color: var(--paper-white); font-family: "Parisienne", cursive;
    font-size: 30px; line-height: 1.2; text-align: center;
  }
  /* Back */
  .card-back { background: var(--brand-blue); }
  .paw-area {
    position: absolute; left: -40px; top: 150px; width: 470px; height: 320px;
    border-radius: 48% 52% 0 0 / 60% 60% 0 0;
    background: var(--paper-white);
  }
  .back-brand {
    position: absolute; left: 80px; top: 270px; color: var(--brand-blue);
  }
  .back-brand .wordmark { font-size: 50px; }
  .back-brand .tagline { font-size: 15px; margin-left: 26px; }
  .holder {
    position: absolute; right: 44px; top: 40px; text-align: right; color: var(--paper-white);
  }
  .holder-name { font-weight: 700; font-size: 24px; letter-spacing: .5px; }
  .holder-title { font-weight: 300; font-size: 16px; }
  .contact-list {
    position: absolute; right: 44px; top: 200px; list-style: none;
    color: var(--paper-white); font-size: 15px; line-height: 1.5; text-align: right;
  }
  .contact-list li { display: flex; justify-content: flex-end; align-items: center; gap: 8px; }
  .contact-icon { width: 14px; height: 14px; fill: var(--paper-white); flex: none; }
  .contact-spacer { width: 14px; flex: none; }
</style>
</head>
<body>
<main class="stage">
  <section class="card card-front">
    <div class="photo-area" role="img" aria-label="Black and white photo of an older dog lying down, gently held by a person's hands"></div>
    <div class="front-brand">
      <div class="wordmark"><span class="wordmark-dot"></span>Hearthwell</div>
      <p class="tagline">A gift of love at home.</p>
    </div>
    <p class="description">Peaceful &amp; Compassionate<br>At-Home Pet Euthanasia</p>
  </section>

  <section class="card card-back">
    <div class="paw-area" role="img" aria-label="Large white paw print decoration"></div>
    <div class="back-brand">
      <div class="wordmark"><span class="wordmark-dot"></span>Hearthwell</div>
      <p class="tagline">A gift of love at home.</p>
    </div>
    <div class="holder">
      <p class="holder-name">DANIEL REYES</p>
      <p class="holder-title">President</p>
    </div>
    <ul class="contact-list">
      <li>412 Willow Bend Road
        <svg class="contact-icon" viewBox="0 0 24 24"><path d="M12 2a7 7 0 0 0-7 7c0 5 7 13 7 13s7-8 7-13a7 7 0 0 0-7-7zm0 9.5A2.5 2.5 0 1 1 12 6.5a2.5 2.5 0 0 1 0 5z"/></svg></li>
      <li>Juneau, Alaska 99801 <span class="contact-spacer"></span></li>
      <li>555-014-2290
        <svg class="contact-icon" viewBox="0 0 24 24"><path d="M6.6 10.8a15 15 0 0 0 6.6 6.6l2.2-2.2a1 1 0 0 1 1-.25 11.4 11.4 0 0 0 3.6.6 1 1 0 0 1 1 1V20a1 1 0 0 1-1 1A17 17 0 0 1 3 4a1 1 0 0 1 1-1h3.5a1 1 0 0 1 1 1c0 1.25.2 2.45.6 3.6a1 1 0 0 1-.25 1z"/></svg></li>
      <li>daniel@hearthwell.com
        <svg class="contact-icon" viewBox="0 0 24 24"><path d="M3 5h18v14H3zm2 2v.5l7 4.5 7-4.5V7l-7 4.5z"/></svg></li>
      <li>www.hearthwell.com
        <svg class="contact-icon" viewBox="0 0 24 24"><circle cx="12" cy="12" r="10"/></svg></li>
    </ul>
  </section>
</main>
</body>
</html>
```